Restyle corporate identity (+ logo) for a road construction company

We need a new logo and stationary design for our company VARNOK path. VARNOK path® increases the road base strength, while reducing major costs and time of road construction. Attached some examples of the current design.

Our wishes for the new logo:
- Business look
- Style sheet
- Modern

More information: www.varnokpath.example
Updates

Target Market(s)

Government

Industry/Entity Type

Construction

Requirements
Must have
• Logo (with road sign) + text

```html
<!DOCTYPE html>
<html lang="en">
<head>
<meta charset="utf-8">
<title>VARNOK path – Business Card</title>
<link href="https://fonts.googleapis.com/css2?family=Open+Sans:wght@400;600;700&display=swap" rel="stylesheet">
<style>
  :root {
    --backdrop: #858585;
    --paper: #eeeff0;
    --brand-green: #6f8c1d;
    --accent-green: #7fa21f;
    --ink-grey: #6b6d70;
    --ink-dark: #4a4c4f;
    --paper-light: #e9ecea;
  }
  * { margin: 0; padding: 0; box-sizing: border-box; }
  html, body {
    width: 1105px; height: 1200px; overflow: hidden;
    background: var(--backdrop);
    font-family: "Open Sans", Arial, sans-serif;
  }
  .card {
    position: absolute;
    left: 182px;
    width: 746px;
    height: 426px;
  }
  .card--front { top: 120px; background: var(--paper); }
  .card--back { top: 635px; background: var(--brand-green); }

  .brand {
    position: absolute;
    display: flex;
    align-items: center;
    gap: 18px;
  }
  .brand__mark { width: 72px; height: 96px; }
  .brand__name {
    font-weight: 700;
    font-size: 52px;
    letter-spacing: 1px;
    line-height: 1;
  }
  .card--front .brand { left: 0; top: 50px; }
  .card--front .brand__mark { background: var(--accent-green); }
  .card--front .brand__name { color: var(--ink-grey); }

  .holder {
    position: absolute;
    top: 210px; left: 0; width: 100%;
    text-align: center;
  }
  .holder__name {
    color: var(--accent-green);
    font-weight: 600;
    font-size: 24px;
    line-height: 30px;
  }
  .holder__role {
    color: var(--ink-grey);
    font-size: 19px;
    line-height: 26px;
  }

  .contact-list {
    position: absolute;
    left: 52px; top: 296px;
    list-style: none;
    color: var(--ink-dark);
    font-size: 19px;
    line-height: 28.5px;
  }
  .contact-list li { display: flex; align-items: center; gap: 10px; }
  .contact-list svg { width: 17px; height: 17px; fill: var(--accent-green); }

  .address {
    position: absolute;
    right: 46px; top: 296px;
    text-align: right;
    font-style: normal;
    color: var(--ink-dark);
    font-size: 19px;
    line-height: 28.5px;
  }

  .card--back .brand {
    left: 0; width: 100%; top: 165px;
    justify-content: center;
  }
  .card--back .brand__mark { width: 60px; height: 80px; background: var(--paper-light); }
  .card--back .brand__name { color: var(--paper-light); font-size: 56px; }
  .back-url {
    position: absolute;
    top: 360px; left: 0; width: 100%;
    text-align: center;
    color: var(--paper-light);
    font-size: 18px;
    letter-spacing: 4px;
  }
</style>
</head>
<body>
  <section class="card card--front">
    <div class="brand">
      <span class="brand__mark"></span>
      <span class="brand__name">VARNOK path</span>
    </div>

    <div class="holder">
      <p class="holder__name">MAREN HOLT</p>
      <p class="holder__role">CEO/Founder</p>
    </div>

    <ul class="contact-list">
      <li>
        <svg viewBox="0 0 24 24" aria-hidden="true"><path d="M6.6 10.8a15.1 15.1 0 0 0 6.6 6.6l2.2-2.2a1 1 0 0 1 1-.25 11.4 11.4 0 0 0 3.6.57 1 1 0 0 1 1 1V20a1 1 0 0 1-1 1A17 17 0 0 1 3 4a1 1 0 0 1 1-1h3.5a1 1 0 0 1 1 1c0 1.25.2 2.45.57 3.6a1 1 0 0 1-.25 1z"/></svg>
        555 210 4817
      </li>
      <li>
        <svg viewBox="0 0 24 24" aria-hidden="true"><path d="M2 5h20v2l-10 6L2 7z"/><path d="M2 9l10 6 10-6v10H2z"/></svg>
        info@varnokpath.example
      </li>
      <li>
        <svg viewBox="0 0 24 24" aria-hidden="true"><path d="M12 2a10 10 0 1 0 0 20 10 10 0 0 0 0-20zm-1 17.9A8 8 0 0 1 4.2 10l4.8 4.8v1a2 2 0 0 0 2 2zm6.9-2.5A2 2 0 0 0 16 16h-1v-3a1 1 0 0 0-1-1H8v-2h2a1 1 0 0 0 1-1V7h2a2 2 0 0 0 2-2v-.4a8 8 0 0 1 2.9 12.8z"/></svg>
        www.varnokpath.example
      </li>
    </ul>

    <address class="address">
      Lindenkade 58<br>
      3012 AB Rotterdam<br>
      The Netherlands
    </address>
  </section>

  <section class="card card--back">
    <div class="brand">
      <span class="brand__mark"></span>
      <span class="brand__name">VARNOK path</span>
    </div>
    <p class="back-url">www.varnokpath.example</p>
  </section>
</body>
</html>
```